Brand Identity Stationary Package

Hello I'm looking for a full branding package for my Property Management Company. I have a logo but looking to have the following
Business Card
Email signature
Facebook cover photo
Letterhead (word.doc)
#10 Envelope
Pocket Folder - link to 9x12 pocket folder design specs https://www.printorbit-example.ca/marketing-materials/presentation-folders
would like everything to match and be brand identifiable. The company looks after residential properties/apartments and some commercial properties. Attached is a zip of the files.
For Business Card
Name: Gareth Lindqvist
Position: Operations Manager
Number: 1 (555) 384-2917
Email: Gareth@harborkey-example.ca
Website: Harborkey-example.ca
Property Management

```html
<!DOCTYPE html>
<html lang="en">
<head>
<meta charset="utf-8">
<title>Harborkey Letterhead</title>
<link rel="stylesheet" href="https://fonts.googleapis.com/css2?family=Montserrat:wght@400;500;700&display=swap">
<style>
  :root {
    --backdrop: #e9e9ea;
    --paper: #ffffff;
    --ink: #111111;
    --brand-green: #86b03a;
    --text: #1b1b1b;
  }
  * { margin: 0; padding: 0; box-sizing: border-box; }
  html, body {
    width: 1200px;
    height: 874px;
    overflow: hidden;
    background: var(--backdrop);
    font-family: "Montserrat", Arial, sans-serif;
  }
  .letterhead {
    position: absolute;
    left: 300px;
    top: 13px;
    width: 600px;
    height: 848px;
    background: var(--paper);
    box-shadow: 0 4px 18px rgba(0,0,0,0.12);
    overflow: hidden;
  }
  .brand {
    position: absolute;
    left: 44px;
    top: 74px;
    display: flex;
    align-items: center;
    gap: 8px;
  }
  .brand-mark {
    width: 12px;
    height: 12px;
    background: var(--brand-green);
  }
  .brand-name {
    font-weight: 700;
    font-size: 26px;
    letter-spacing: 2px;
    color: var(--ink);
    text-transform: uppercase;
    line-height: 1;
  }
  .brand-tagline {
    position: absolute;
    left: 64px;
    top: 104px;
    font-weight: 500;
    font-size: 7.5px;
    letter-spacing: 4.2px;
    color: var(--ink);
    text-transform: uppercase;
  }
  .contact {
    position: absolute;
    left: 392px;
    top: 40px;
    padding-left: 12px;
    border-left: 1px solid var(--brand-green);
    color: var(--text);
    font-size: 10px;
    line-height: 1.45;
  }
  .contact-name {
    color: var(--brand-green);
    font-weight: 700;
    text-transform: uppercase;
    font-size: 10.5px;
  }
  .contact-role { margin-bottom: 3px; }
  .contact-line {
    display: flex;
    align-items: center;
    gap: 7px;
  }
  .contact-line svg {
    width: 9px;
    height: 9px;
    fill: var(--brand-green);
    flex: none;
  }
  .footer-band {
    position: absolute;
    left: 0;
    bottom: 0;
    width: 600px;
    height: 30px;
  }
  .band-dark { fill: var(--ink); }
  .band-accent { fill: var(--brand-green); }
</style>
</head>
<body>
  <main class="letterhead">
    <header>
      <div class="brand">
        <span class="brand-mark"></span>
        <span class="brand-name">Harborkey</span>
      </div>
      <div class="brand-tagline">Property Management</div>

      <address class="contact" style="font-style:normal">
        <div class="contact-name">Gareth Lindqvist</div>
        <div class="contact-role">Operations Manager</div>
        <div class="contact-line">
          <svg viewBox="0 0 24 24"><path d="M6.6 10.8a15 15 0 0 0 6.6 6.6l2.2-2.2c.3-.3.7-.4 1-.2 1.1.4 2.3.6 3.6.6.6 0 1 .4 1 1V20c0 .6-.4 1-1 1A17 17 0 0 1 3 4c0-.6.4-1 1-1h3.5c.6 0 1 .4 1 1 0 1.3.2 2.5.6 3.6.1.3 0 .7-.2 1z"/></svg>
          <span>1 (555) 384-2917</span>
        </div>
        <div class="contact-line">
          <svg viewBox="0 0 24 24"><path d="M2 5h20v14H2z M2 5l10 8 10-8" stroke="#fff" stroke-width="1.5"/></svg>
          <span>Gareth@harborkey-example.ca</span>
        </div>
        <div class="contact-line">
          <svg viewBox="0 0 24 24"><circle cx="12" cy="12" r="10"/><path d="M2 12h20M12 2c3 3 3 17 0 20M12 2c-3 3-3 17 0 20" stroke="#fff" stroke-width="1.3" fill="none"/></svg>
          <span>Harborkey-example.ca</span>
        </div>
      </address>
    </header>

    <svg class="footer-band" viewBox="0 0 600 30" aria-hidden="true">
      <polygon class="band-dark" points="0,8 348,8 338,30 0,30"/>
      <polygon class="band-accent" points="354,0 600,0 600,30 344,30"/>
    </svg>
  </main>
</body>
</html>
```